Basic / Quick Business Card

Quick easy design project!

Need a one sided basic business card that matches font & style of brand and bottle label for our gourmet condiment, Brindle Harrow Sauce. Brindle Harrow Sauce is sold in specialty retail, gourmet groceries and appears on chef-driven restaurant menus, so the target market is a high end, gourmet, artisan-made food-loving customer.

Files Included:
Sauce Bottle Label
Brindle Harrow Sauce Round Logos

**About the logos - the logo may be used in a circle or alone vertically as on side of the bottle label**

Layout of Card:
May be vertical or horizontal based on designer ideas.

Logo usage (in circle vs. stand alone vertical logo) is up to designers descretion as well.

Reverse side of business card will be various high end / professional product photos / food shots using us.kelbo.com system. **Designer on this project will NOT design a reserve for the card.**

Paper that will be used for printing:
Kelbo Standard - it's a WHITE paper, but we use a cream background on Brindle Harrow Sauce branding, so please take this into account on design to stay brand consistent.

Elements & Copy for Card:
1. Logo in either script horizontal or vertical version
2. Copy: "Artisan Made - Small Batch"
3. Name - Wes Dorrance
4. Title - Creator
5. Phone - xxx.xxx.xxxx
6. xxxx@brindleharrow.com
7. URL: brindleharrowsauce.com
8. Social Media: @getbrindleharrow on Quillo / Pagora / Lumigrid

Please provide final files in Illustrator or InDesign format.

```html
<!DOCTYPE html>
<html lang="en">
<head>
<meta charset="utf-8">
<title>Brindle Harrow Sauce — Business Card</title>
<link rel="stylesheet" href="https://fonts.googleapis.com/css2?family=Fondamento&display=swap">
<style>
  :root {
    --backdrop: #d8d3c6;
    --card-dark: #231f20;
    --cream: #ecebd7;
    --gold: #f0b323;
    --ink: #231f20;
    --white: #ffffff;
    --type: "Fondamento", Georgia, serif;
  }
  * { box-sizing: border-box; margin: 0; padding: 0; }
  html, body {
    width: 1200px;
    height: 804px;
    overflow: hidden;
    background: var(--backdrop);
  }
  .card {
    position: absolute;
    left: 100px;
    top: 116px;
    width: 1000px;
    height: 572px;
    background: var(--card-dark);
    overflow: hidden;
    font-family: var(--type);
    color: var(--ink);
  }
  .brand-seal {
    position: absolute;
    left: 114px;
    top: 59px;
    width: 232px;
    height: 232px;
    border-radius: 50%;
    background: var(--cream);
    border: 7px solid var(--gold);
    box-shadow: 0 0 0 3px var(--cream) inset;
    display: flex;
    flex-direction: column;
    align-items: center;
    justify-content: center;
    text-align: center;
  }
  .brand-seal::before {
    content: "";
    position: absolute;
    inset: 6px;
    border-radius: 50%;
    border: 2px solid var(--ink);
  }
  .brand-name {
    font-size: 36px;
    line-height: 1.05;
    color: var(--ink);
  }
  .tagline-badge {
    position: absolute;
    left: 118px;
    top: 436px;
    width: 214px;
    height: 140px;
  }
  .tagline-badge svg { position: absolute; inset: 0; }
  .tagline-text {
    position: absolute;
    left: 0;
    right: 0;
    top: 58px;
    text-align: center;
    font-size: 22px;
    line-height: 1.1;
    color: var(--ink);
  }
  .contact-panel {
    position: absolute;
    left: 525px;
    top: 34px;
    width: 440px;
    height: 500px;
    background: var(--cream);
  }
  .contact-list {
    list-style: none;
    position: absolute;
    left: 30px;
    top: 42px;
  }
  .contact-list li {
    display: flex;
    align-items: center;
    height: 48px;
    font-size: 25px;
  }
  .contact-list svg {
    width: 22px;
    height: 22px;
    margin-right: 12px;
    flex: none;
  }
  .dotted-rule {
    position: absolute;
    left: 30px;
    right: 20px;
    border-top: 4px dotted var(--gold);
  }
  .rule-top { top: 206px; }
  .rule-bottom { top: 306px; }
  .social {
    position: absolute;
    left: 30px;
    top: 236px;
    display: flex;
    align-items: center;
    font-size: 22px;
    gap: 14px;
  }
  .social-handle {
    display: flex;
    align-items: center;
    gap: 5px;
    font-size: 17px;
  }
  .social-handle::before {
    content: "";
    width: 12px;
    height: 12px;
    border-radius: 50%;
    background: var(--gold);
  }
  .flavor {
    position: absolute;
    left: 44px;
    top: 346px;
    font-size: 25px;
  }
  .name-band {
    position: absolute;
    left: 15px;
    right: 10px;
    top: 415px;
    height: 66px;
    background: var(--gold);
    color: var(--white);
    font-size: 31px;
    display: flex;
    align-items: center;
    padding-left: 20px;
  }
</style>
</head>
<body>
  <main class="card">
    <div class="brand-seal">
      <span class="brand-name">Brindle<br>Harrow<br>Sauce</span>
    </div>

    <div class="tagline-badge">
      <svg viewBox="0 0 214 140" width="214" height="140" aria-hidden="true">
        <polygon points="4,50 100,6 210,40 210,140 4,140" fill="var(--gold)" stroke="var(--cream)" stroke-width="7" stroke-linejoin="miter"/>
      </svg>
      <p class="tagline-text">Artisan Made<br>Small Batch</p>
    </div>

    <section class="contact-panel">
      <ul class="contact-list">
        <li>
          <svg viewBox="0 0 24 24" aria-hidden="true"><circle cx="12" cy="12" r="10.5" fill="none" stroke="var(--ink)" stroke-width="2"/><path d="M8.5 6.5l2 2.5-1.2 1.4c.7 1.6 1.8 2.7 3.3 3.4l1.4-1.2 2.5 2-1.3 2c-4.4-.4-7.7-3.7-8.1-8.2z" fill="var(--ink)"/></svg>
          555-204-7731
        </li>
        <li>
          <svg viewBox="0 0 24 24" aria-hidden="true"><rect x="2" y="5" width="20" height="14" rx="2" fill="var(--ink)"/><path d="M3 6l9 7 9-7" fill="none" stroke="var(--cream)" stroke-width="1.8"/></svg>
          wdorrance@brindleharrow.com
        </li>
        <li>
          <svg viewBox="0 0 24 24" aria-hidden="true"><circle cx="12" cy="12" r="10" fill="none" stroke="var(--ink)" stroke-width="2"/><ellipse cx="12" cy="12" rx="4.5" ry="10" fill="none" stroke="var(--ink)" stroke-width="1.6"/><path d="M2 12h20M4 7h16M4 17h16" stroke="var(--ink)" stroke-width="1.6"/></svg>
          www.brindleharrowsauce.com
        </li>
      </ul>

      <hr class="dotted-rule rule-top">
      <div class="social">
        <span>Follow Us On</span>
        <span class="social-handle">Pagora</span>
        <span class="social-handle">Quillo</span>
        <span class="social-handle">Lumigrid</span>
      </div>
      <hr class="dotted-rule rule-bottom">

      <p class="flavor">sweet &amp; spicy</p>

      <div class="name-band">Wes Dorrance, Creator</div>
    </section>
  </main>
</body>
</html>
```